Business Card - high end, modern health care

Hey designers!

We need a double sided business card for the boutique, cutting edge physical therapy rehabilitation centre in Sydney's Northern Beaches.

With the most qualified physios in the area The Harbourview Motion Clinic does what other physiotherapy practices do not, we take our time with our patients giving them longer appointments, better physios and therefor faster results!

We guarantee that the service people receive at THMC will be unparalleled.

Hence we need a business card to reflect our modern, boutique, high end service. The final design needs to reflect that we are in a class of our own yet with the feel of beachside retreat.

Below I have attached our logo in both blue on white and white on blue. The exact colour is;
and the font that we have used in our logo is Tex Gyre Aventador.

I like the idea of the blue as the main colour as it is more eye catching and our signage onto the main road will be in this blue and in the interest of consistency across marketing the blue needs to be a part of the design. However I would appreciate a few designs onto a wooden background as this is a visual theme within the fitout of the practice.

The design needs to be of standard size (91x55mm).

Target Market(s)

We target people who have an end outcome in mind and those who have had poor experiences with other providers and ensure that everyone gets the care that they deserve with a premium service that is tailored to the individuals circumstances. As a premium service, the target market is highly educated, business and tech savvy with the additional target market of elderly people who have self funded their retirement and see value in paying for the best ongoing rehabilitation to maintain independence.

Industry/Entity Type

Physical Therapy

Contact Information for Business Card

Name, designation( Titled Musculoskeletal Physiotherapist... there will also be those in the company that have multiple designations ie 5 or 6 words long), phone number, email, facebook, instagram, address

Font styles to use
Sans Serif

Colors

Designer to choose colors to be used in the design.

Requirements
Must have
• Front - The logo as large as possible, blue or wooden theme, and all of the important details.
• Back - A blank space/lines on which to write appointment times (no "Appointment, date, time" etc.)
Nice to have
• facebook url
• logos for facebook and instagram
• Mini logos for the phone and email?

```html
<!DOCTYPE html>
<html lang="en">
<head>
<meta charset="utf-8">
<title>The Harbourview Motion Clinic – Business Card</title>
<link href="https://fonts.googleapis.com/css2?family=Roboto:wght@400;500;700&family=Roboto+Condensed:wght@400;700&display=swap" rel="stylesheet">
<style>
  :root {
    --stage: #2b2e33;
    --brand-blue: #1730c8;
    --brand-blue-deep: #0a1a8f;
    --brand-blue-bright: #2346ff;
    --silver: #d9d9d9;
    --silver-dark: #9a9a9a;
    --paper: #f4f5f7;
    --ink-white: #ffffff;
  }
  * { margin: 0; padding: 0; box-sizing: border-box; }
  html, body { width: 1200px; height: 900px; overflow: hidden; }
  body { background: var(--stage); position: relative; font-family: "Roboto", sans-serif; }

  .card {
    position: absolute;
    left: 270px;
    width: 660px;
    height: 399px;
    border-radius: 26px;
    overflow: hidden;
    box-shadow: 0 10px 30px rgba(0,0,0,0.45);
  }
  .card-front { top: 31px; background: linear-gradient(135deg, var(--brand-blue-deep), var(--brand-blue) 45%, var(--brand-blue-bright)); }
  .card-back { top: 470px; background: var(--paper); }

  .card-art { position: absolute; inset: 0; }

  /* front */
  .brand-lockup-front {
    position: absolute; left: 40px; top: 262px; width: 280px;
    text-align: center; color: var(--silver);
    font-family: "Roboto", sans-serif; font-weight: 500;
    font-size: 21px; letter-spacing: 3px; line-height: 1.25; text-transform: uppercase;
  }
  .holder {
    position: absolute; right: 40px; top: 46px; text-align: right; color: var(--ink-white);
  }
  .holder-name { font-family: "Roboto", sans-serif; font-weight: 700; font-size: 36px; letter-spacing: 1px; text-transform: uppercase; }
  .holder-title { font-family: "Roboto Condensed", sans-serif; font-size: 18px; margin-top: 2px; }

  .treatment-art {
    position: absolute; top: 138px; width: 62px; height: 44px; border-radius: 6px;
    background: linear-gradient(180deg, rgba(255,255,255,0.85), rgba(220,225,240,0.75));
  }
  .treatment-art.first { right: 128px; }
  .treatment-art.second { right: 42px; top: 170px; }

  .contact-list {
    position: absolute; right: 40px; top: 226px; list-style: none;
    font-family: "Roboto Condensed", sans-serif; font-size: 17px; color: var(--ink-white);
  }
  .contact-list li { display: flex; align-items: center; justify-content: flex-end; gap: 10px; height: 28px; }
  .contact-icon { width: 20px; height: 20px; flex: none; }
  .social-mark { width: 18px; height: 18px; border-radius: 3px; background: var(--ink-white); flex: none; margin: 0 1px; }

  /* back */
  .brand-lockup-back {
    position: absolute; left: 250px; top: 186px; width: 300px; text-align: center;
    color: var(--brand-blue); font-family: "Roboto", sans-serif; font-weight: 500;
    font-size: 17px; letter-spacing: 2.5px; text-transform: uppercase; line-height: 1.2;
  }
  .appointment {
    position: absolute; left: 40px; top: 292px; display: flex; align-items: center; gap: 12px;
    color: var(--brand-blue); font-family: "Roboto Condensed", sans-serif; font-size: 18px;
  }
  .appointment-arrow { width: 26px; height: 22px; }
  .appointment-line { width: 300px; border-bottom: 1.5px dashed var(--brand-blue); align-self: flex-end; margin-bottom: 4px; }
</style>
</head>
<body>

<section class="card card-front" aria-label="Card front">
  <svg class="card-art" viewBox="0 0 660 399" aria-hidden="true">
    <defs>
      <linearGradient id="silverFill" x1="0" y1="0" x2="1" y2="1">
        <stop offset="0" stop-color="#f0f0f0"/>
        <stop offset="0.5" stop-color="#b8b8b8"/>
        <stop offset="1" stop-color="#e2e2e2"/>
      </linearGradient>
    </defs>
    <path d="M330 0 Q338 270 140 399" fill="none" stroke="#05082a" stroke-width="6"/>
    <path d="M322 0 Q330 266 132 399" fill="none" stroke="url(#silverFill)" stroke-width="4"/>
    <circle cx="180" cy="135" r="108" fill="url(#silverFill)"/>
  </svg>

  <div class="brand-lockup-front">The Harbourview<br>Motion Clinic</div>

  <div class="holder">
    <div class="holder-name">Daniel Reyes</div>
    <div class="holder-title">Musculoskeletal Physiotherapist</div>
  </div>

  <div class="treatment-art first" role="img" aria-label="Icon of a therapist treating a patient on a table"></div>
  <div class="treatment-art second" role="img" aria-label="Icon of a patient receiving assisted stretching"></div>

  <ul class="contact-list">
    <li>48 Shoreline Rd, Dee Why NSW
      <svg class="contact-icon" viewBox="0 0 20 20" aria-hidden="true"><path d="M10 1a6 6 0 0 0-6 6c0 4.5 6 12 6 12s6-7.5 6-12a6 6 0 0 0-6-6z" fill="#fff"/><circle cx="10" cy="7" r="2.2" fill="var(--brand-blue)"/></svg>
    </li>
    <li>+00 210 456 789
      <svg class="contact-icon" viewBox="0 0 20 20" aria-hidden="true"><rect x="1" y="1" width="18" height="18" rx="3" fill="#fff"/><path d="M6.5 4.5l2 2.5-1.2 1.3c.8 1.7 2 2.9 3.6 3.7l1.3-1.2 2.4 2-1.3 2c-4.5-.4-8.3-4.2-8.7-8.7z" fill="var(--brand-blue)"/></svg>
    </li>
    <li>Hello@Harbourview.com
      <svg class="contact-icon" viewBox="0 0 20 20" aria-hidden="true"><rect x="1" y="1" width="18" height="18" rx="3" fill="#fff"/><rect x="4" y="6" width="12" height="8" fill="none" stroke="var(--brand-blue)" stroke-width="1.4"/><path d="M4 6l6 5 6-5" fill="none" stroke="var(--brand-blue)" stroke-width="1.4"/></svg>
    </li>
    <li>Social/Harbourview <span class="social-mark"></span></li>
    <li>@harbourviewmotion <span class="social-mark"></span></li>
  </ul>
</section>

<section class="card card-back" aria-label="Card back">
  <svg class="card-art" viewBox="0 0 660 399" aria-hidden="true">
    <circle cx="400" cy="105" r="78" fill="var(--brand-blue)"/>
    <line x1="0" y1="244" x2="660" y2="244" stroke="var(--brand-blue)" stroke-width="3"/>
    <line x1="0" y1="256" x2="660" y2="256" stroke="var(--brand-blue)" stroke-width="3"/>
  </svg>

  <div class="brand-lockup-back">The Harbourview<br>Motion Clinic</div>

  <div class="appointment">
    <svg class="appointment-arrow" viewBox="0 0 26 22" aria-hidden="true"><path d="M0 0L26 11 0 22 6 11z" fill="var(--brand-blue)"/></svg>
    <span>Appointment Times:</span>
    <span class="appointment-line"></span>
  </div>
</section>

</body>
</html>
```